Spy/Espionage/Counterintelligence Membership Community Needs a PowerPoint Template

We need a powerpoint template for one of our business verticals focused on spies, espionage, and counterintelligence. The name of it is "Brass Lantern Guild" and the logo is attached. Brass Lantern Guild is a community that connects people with experts in espionage and counterintelligence through an online social network, as well as in-person events. We would like to see designs that incorporate the red and black of the logo. The design should communicate mystery/suspense and peak curiosity.

Target Market(s)

Late 20s to baby boomers, male

Industry/Entity Type

Social Club

Font styles to use
Sans Serif

Colors
ec1f27
000000
ffffff

Requirements
Must have
• A user-friendly ppt template file. Incorporate basic fonts that don't have to be installed on every computer for presentations. A cover slide and a basic inside slide. A white background. I will also need graphic source files.
Nice to have
• Plenty of space for slide title and body content. Logo on every slide.
Should not have
• Inconsistency with fonts. Misalignment of images.

```html
<!DOCTYPE html>
<html lang="en">
<head>
<meta charset="utf-8">
<title>Brass Lantern Guild – Inside Slide</title>
<link href="https://fonts.googleapis.com/css2?family=Questrial&display=swap" rel="stylesheet">
<style>
  :root {
    --brand-red: #c40000;
    --accent-red: #ec1f27;
    --ink: #000000;
    --paper: #ffffff;
    --body-text: #4a4a4a;
    --placeholder: #e0dfe0;
    --watermark: #ededed;
    --footer: #1a1a1a;
    --rule: #333333;
  }
  * { margin: 0; padding: 0; box-sizing: border-box; }
  html, body { width: 1200px; height: 900px; overflow: hidden; background: var(--paper); }
  body { font-family: "Questrial", "Century Gothic", sans-serif; }

  .slide { position: relative; width: 1200px; height: 900px; overflow: hidden; background: var(--paper); }

  .backdrop-circle { position: absolute; left: 0; top: 0; }

  .slide-header {
    position: absolute; left: 0; top: 0; width: 1200px; height: 72px;
    background: var(--brand-red);
    border-bottom: 3px solid var(--paper);
    box-shadow: 0 3px 0 var(--rule);
  }
  .slide-title {
    position: absolute; left: 21px; top: 11px;
    color: var(--paper); font-size: 45px; font-weight: 400; letter-spacing: 0.3px;
  }
  .brand {
    position: absolute; right: 10px; top: 10px; display: flex; align-items: center; gap: 10px;
  }
  .brand-dot { width: 50px; height: 50px; border-radius: 50%; background: var(--ink); }
  .brand-name { color: var(--ink); font-size: 29px; letter-spacing: -0.5px; }

  .content-block { position: absolute; left: 31px; }
  .section-heading {
    position: absolute; left: 42px; top: 158px;
    color: var(--brand-red); font-size: 25px; font-weight: 700;
  }
  .body-copy { color: var(--body-text); font-size: 20.5px; line-height: 36px; white-space: nowrap; }
  .copy-one { top: 188px; }
  .copy-two { top: 489px; }

  .media-slot { position: absolute; left: 675px; width: 485px; height: 237px; background: var(--placeholder); }
  .media-top { top: 186px; }
  .media-bottom { top: 518px; }

  .slide-footer {
    position: absolute; left: 0; top: 856px; width: 1200px; height: 44px; background: var(--footer);
  }
  .copyright { position: absolute; left: 10px; top: 10px; color: var(--paper); font-size: 20px; }
  .page-number {
    position: absolute; left: 1159px; top: 5px; width: 34px; height: 34px; border-radius: 50%;
    background: var(--brand-red); border: 2px solid var(--paper);
    color: var(--paper); font-size: 18px; line-height: 30px; text-align: center;
  }
</style>
</head>
<body>
<div class="slide">
  <svg class="backdrop-circle" width="440" height="900" viewBox="0 0 440 900" aria-hidden="true">
    <circle cx="60" cy="465" r="370" fill="var(--watermark)"/>
  </svg>

  <header class="slide-header">
    <h1 class="slide-title">Project Title Here</h1>
    <div class="brand">
      <span class="brand-dot"></span>
      <span class="brand-name">Brass Lantern Guild</span>
    </div>
  </header>

  <h2 class="section-heading">Lorem ipsum dolor sit Lorem</h2>

  <p class="content-block body-copy copy-one">
    Lorem ipsum dolor sit Lorem ipsum dolor sit&nbsp; Lorem<br>
    ipsum dolor sit Lorem ipsum dolor sit&nbsp; Lorem ipsum<br>
    dolor sit Lorem ipsum dolor sit&nbsp; Lorem ipsum dolor sit<br>
    Lorem ipsum dolor sit&nbsp; Lorem ipsum dolor sit Lorem<br>
    ipsum dolor sit&nbsp; Lorem ipsum dolor sit Lorem ipsum<br>
    dolor sit&nbsp; Lorem ipsum dolor sit Lorem ipsum dolor sit<br>
    Lorem ipsum dolor sit Lorem ipsum dolor sit
  </p>

  <p class="content-block body-copy copy-two">
    Lorem ipsum dolor sit Lorem ipsum dolor sit&nbsp; Lorem<br>
    ipsum dolor sit Lorem ipsum dolor sit&nbsp; Lorem ipsum<br>
    dolor sit Lorem ipsum dolor sit&nbsp; Lorem ipsum dolor sit<br>
    Lorem ipsum dolor sit&nbsp; Lorem ipsum dolor sit Lorem<br>
    ipsum dolor sit&nbsp; Lorem ipsum dolor sit Lorem ipsum<br>
    dolor sit&nbsp; Lorem ipsum dolor sit Lorem ipsum dolor sit<br>
    Lorem ipsum dolor sit Lorem ipsum dolor sit
  </p>

  <div class="media-slot media-top" role="img" aria-label="Image placeholder"></div>
  <div class="media-slot media-bottom" role="img" aria-label="Image placeholder"></div>

  <footer class="slide-footer">
    <span class="copyright">Copyright text here</span>
    <span class="page-number">1</span>
  </footer>
</div>
</body>
</html>
```